Business card design for a dynamic IT consulting company

We need a business card design for a young firm, specialized in the Telecommunications/Consulting industry. The name of the company is Quindor and Partners Business Consulting Ltd. (Short name: Quindor and Partnes)
Quindor = solve read reverse, so we aim to be uncomplicated and solution-oriented. The small pipe in our logo is also related to the word solve. So we need a new business card design, which is simple, eye catching and something non traditional (I would probably prefer a square shaped design rather than a rectangle, but open for suggestions). Attached our logo.

Target Market(s)

Usually our customers are Tier1 Telecoms providers (Q-Netra, Palorix, etc) and their executives.

Industry/Entity Type

Business

Contact Information for Business Card

Name: Bence Tolnavari
Email: b.tolnavari@quindor.hu
Web: www.quindor.hu
Mobile: +36 30 518 2769
Title: Managing Director

Optional:
Company name: Quindor and Partners Ltd.
Address: 1087 Budapest, Tolvenka str. 28/C, Hungary

Font styles to use
Other font styles liked:
• helveticaneue_medium, Prime Regular are used now.

Colors

Designer to choose colors to be used in the design.

Requirements
Must have
• I would like to have a 2 sided design.
Nice to have
• I thought if we make the logo a bit bigger (without the company name), that could go to the back with the company name below. I though, if the pipe in the logo is somehow touchable on the business card, would be nice and unique.

```html
<!DOCTYPE html>
<html lang="en">
<head>
<meta charset="utf-8">
<title>Quindor &amp; Partners — Business Card</title>
<link rel="stylesheet" href="https://fonts.googleapis.com/css2?family=Arimo:wght@400;700&family=Questrial&display=swap">
<style>
  :root {
    --backdrop: #e2e2e2;
    --card: #f7f7f7;
    --ink: #505052;
    --ink-soft: #5c5c5e;
    --accent-blue: #1b9ad8;
    --band: #5a5a5c;
    --on-band: #ffffff;
    --tint-pink: #efcfe2;
    --tint-blue: #cfe6f2;
    --tint-grey: #dcdcdc;
  }
  * { margin: 0; padding: 0; box-sizing: border-box; }
  html, body {
    width: 1200px; height: 960px; overflow: hidden;
    background: var(--backdrop);
  }
  .stage { position: relative; width: 1200px; height: 960px; }
  .card {
    position: absolute; top: 305px;
    width: 343px; height: 343px;
    background: var(--card);
    overflow: hidden;
    font-family: "Arimo", Helvetica, Arial, sans-serif;
  }
  .card--front { left: 200px; }
  .card--back { left: 651px; }

  /* front */
  .brand {
    position: absolute; left: 0; right: 0;
    text-align: center;
    font-family: "Questrial", "Helvetica Neue", sans-serif;
    color: var(--ink);
    white-space: nowrap;
  }
  .brand__mark {
    display: inline-block; width: 10px; height: 10px;
    background: var(--accent-blue);
    margin-right: 8px; vertical-align: middle;
  }
  .card--front .brand { top: 33px; font-size: 25px; }
  .person { position: absolute; top: 104px; left: 0; right: 0; text-align: center; }
  .person__name {
    color: var(--accent-blue); font-weight: 700; font-size: 19px; letter-spacing: 0.2px;
  }
  .person__title { color: var(--ink-soft); font-size: 15px; margin-top: 3px; letter-spacing: 0.3px; }
  .address {
    position: absolute; top: 169px; left: 0; right: 0;
    text-align: center; color: var(--ink-soft); font-size: 14px; line-height: 19px;
  }
  .contact-band {
    position: absolute; left: 0; right: 0; bottom: 0; height: 108px;
    background: var(--band);
  }
  .contact-list {
    position: absolute; left: 29px; top: 22px; list-style: none;
    color: var(--on-band); font-size: 13.5px; line-height: 18px;
  }
  .contact-list li { display: flex; align-items: center; gap: 8px; }
  .contact-list svg { width: 12px; height: 12px; flex: none; }
  .band-texture {
    position: absolute; right: 0; top: 0; width: 148px; height: 108px;
    background: linear-gradient(135deg, #6a6a6c 0%, #8a8a8c 100%);
  }

  /* back */
  .card--back .brand { top: 27px; font-size: 33px; }
  .website {
    position: absolute; top: 74px; left: 0; right: 0; text-align: center;
    color: var(--ink-soft); font-size: 13px; letter-spacing: 9.5px;
  }
  .back-texture {
    position: absolute; left: 30px; top: 112px; width: 278px; height: 210px;
    background: linear-gradient(135deg, var(--tint-pink) 0%, var(--tint-blue) 55%, var(--tint-grey) 100%);
    opacity: 0.75;
  }
</style>
</head>
<body>
<main class="stage">

  <section class="card card--front" aria-label="Business card, front">
    <div class="brand"><span class="brand__mark"></span>Quindor &amp; Partners</div>
    <div class="person">
      <p class="person__name">BENCE TOLNAVARI</p>
      <p class="person__title">MANAGING DIRECTOR</p>
    </div>
    <p class="address">Quindor and Partners Ltd., 1087 Budapest<br>Tolvenka str. 28/C, Hungary</p>
    <div class="contact-band">
      <ul class="contact-list">
        <li>
          <svg viewBox="0 0 12 12" aria-hidden="true"><rect x="3" y="0.5" width="6" height="11" rx="1" fill="none" stroke="#fff" stroke-width="1.4"/><rect x="5" y="9" width="2" height="1" fill="#fff"/></svg>
          +36 30 518 2769
        </li>
        <li>
          <svg viewBox="0 0 12 12" aria-hidden="true"><rect x="0.5" y="2.5" width="11" height="7" fill="#fff"/><path d="M0.5 2.5 L6 7 L11.5 2.5" fill="none" stroke="#5a5a5c" stroke-width="1"/></svg>
          b.tolnavari@quindor.hu
        </li>
        <li>
          <svg viewBox="0 0 12 12" aria-hidden="true"><circle cx="6" cy="6" r="5.5" fill="#fff"/><path d="M3 4 Q5 3 5 5 T7 8 M8 2.5 Q7 4.5 9 5" fill="none" stroke="#5a5a5c" stroke-width="1"/></svg>
          www.quindor.hu
        </li>
      </ul>
      <div class="band-texture" role="img" aria-label="Decorative grid of small squares"></div>
    </div>
  </section>

  <section class="card card--back" aria-label="Business card, back">
    <div class="brand">Quindor &amp; Partners</div>
    <p class="website">www.quindor.hu</p>
    <div class="back-texture" role="img" aria-label="Large faint grid of pink, blue and grey squares"></div>
  </section>

</main>
</body>
</html>
```